BWP Business Card

A double sided business card based on your "Brindlewood Partners Ltd" Logo. To use the "BWP" logo on 1 side and the full company logo on the reverse.

Detials to be included:

Name: Tomas Wheeler
Postion: Consultant Orthotist & Expert Witness
T: +44 (0) 7700 938271
F: +44 (0) 7654 8820

```html
<!DOCTYPE html>
<html lang="en">
<head>
<meta charset="utf-8">
<title>BWP Business Card</title>
<link rel="stylesheet" href="https://fonts.googleapis.com/css2?family=Cinzel:wght@600&family=Crimson+Text:wght@400;700&family=Open+Sans:wght@400&display=swap">
<style>
  :root {
    --navy: #0b3c70;
    --grey: #9a9a9a;
    --grey-light: #b5b5b5;
    --white: #ffffff;
    --backdrop: #ececef;
    --text-grey: #8a8a8a;
  }
  * { margin: 0; padding: 0; box-sizing: border-box; }
  html, body {
    width: 1200px; height: 987px; overflow: hidden;
    background: var(--backdrop);
  }
  .sheet {
    width: 1200px; height: 987px;
    display: flex; align-items: center; justify-content: center; gap: 40px;
  }
  .card {
    position: relative;
    width: 540px; height: 336px;
    border-radius: 28px;
    overflow: hidden;
    box-shadow: 0 6px 20px rgba(0,0,0,0.12);
  }

  /* Reverse side */
  .card-back {
    background: var(--navy);
    display: flex; align-items: center; justify-content: center; gap: 18px;
  }
  .card-back .mark-square { width: 46px; height: 46px; background: var(--grey); }
  .card-back .mark-name {
    font-family: "Crimson Text", serif; font-weight: 700;
    font-size: 92px; letter-spacing: 10px; color: var(--grey); line-height: 1;
  }

  /* Front side */
  .card-front { background: var(--white); }
  .card-front .swoosh { position: absolute; inset: 0; width: 100%; height: 100%; }
  .brand-row {
    position: absolute; top: 28px; left: 34px; right: 30px;
    display: flex; align-items: center;
  }
  .brand-mark { display: flex; align-items: center; gap: 10px; padding-right: 18px; }
  .brand-mark .mark-square { width: 22px; height: 22px; background: var(--navy); }
  .brand-mark .mark-name {
    font-family: "Crimson Text", serif; font-weight: 700;
    font-size: 46px; letter-spacing: 4px; color: var(--navy); line-height: 1;
  }
  .brand-divider { width: 1px; height: 86px; background: var(--grey-light); }
  .brand-wording { padding-left: 16px; }
  .company-name {
    font-family: "Cinzel", serif; font-weight: 600;
    font-size: 25px; line-height: 1.05; color: var(--navy);
  }
  .tagline {
    margin-top: 6px; padding-top: 4px;
    border-top: 1px solid var(--grey-light);
    font-family: "Crimson Text", serif; font-size: 10px;
    letter-spacing: 1px; text-transform: uppercase; color: var(--navy);
  }
  .person {
    position: absolute; top: 124px; left: 170px;
    font-family: "Crimson Text", serif;
  }
  .person-name { font-size: 22px; font-weight: 700; color: var(--navy); line-height: 1.1; }
  .person-role { font-size: 16px; color: var(--text-grey); line-height: 1.2; }
  .contacts {
    position: absolute; left: 30px; top: 254px;
    list-style: none;
    font-family: "Open Sans", sans-serif; font-size: 12px; color: var(--white);
  }
  .contacts li { display: flex; align-items: center; gap: 7px; height: 22px; white-space: nowrap; }
  .contacts .gap { width: 8px; }
  .contacts svg { width: 12px; height: 12px; flex: none; }
</style>
</head>
<body>
<main class="sheet">

  <section class="card card-front" aria-label="Business card front">
    <svg class="swoosh" viewBox="0 0 540 336" preserveAspectRatio="none" aria-hidden="true">
      <path d="M0,176 C200,186 400,250 540,300 L540,336 L0,336 Z" fill="var(--grey)"/>
      <path d="M0,192 C200,202 400,266 540,314 L540,336 L0,336 Z" fill="var(--navy)"/>
    </svg>

    <div class="brand-row">
      <div class="brand-mark">
        <span class="mark-square"></span>
        <span class="mark-name">BWP</span>
      </div>
      <span class="brand-divider"></span>
      <div class="brand-wording">
        <p class="company-name">Brindlewood<br>Partners Ltd</p>
        <p class="tagline">Excellence in Medical Legal Reporting</p>
      </div>
    </div>

    <div class="person">
      <p class="person-name">Tomas Wheeler</p>
      <p class="person-role">Consultant Orthotist &amp; Expert Witness</p>
    </div>

    <ul class="contacts">
      <li>18 Alder Row, Kingsbridge, Surrey, KT9 4QP</li>
      <li>
        <svg viewBox="0 0 16 16"><path d="M4 1l3 3-2 2c1 2 3 4 5 5l2-2 3 3-2 3C7 15 1 9 1 3z" fill="currentColor"/></svg>
        +44 (0) 7700 938271
        <span class="gap"></span>
        <svg viewBox="0 0 16 16"><path d="M4 1h8v4H4zM2 6h12v6h-2v3H4v-3H2zM5 10v4h6v-4z" fill="currentColor"/></svg>
        +44 (0) 7654 8820
      </li>
      <li>
        <svg viewBox="0 0 16 16"><path d="M1 3h14v10H1zm1 1v1l6 4 6-4V4z" fill="currentColor"/></svg>
        tomas@brindlewoodpartners.co.uk
      </li>
    </ul>
  </section>

  <section class="card card-back" aria-label="Business card back">
    <span class="mark-square"></span>
    <span class="mark-name">BWP</span>
  </section>

</main>
</body>
</html>
```